Large online photo magazine needs redesign

We have previously digitised a historical photographic magazine of around 20,000 printed pages and made it available online. The magazine ran up to the early 1970s, and the content is largely black and white photographs of local events, accompanied by short captions.

Although the content is very rich, the design needs to be revisited so that:
* it is visually appealing
* it is responsive (i.e. works in browsers across all manner of devices)
* is faithful to the nature of the content

There are only a few core page types, and the central one is the article page, an example of which can be seen at:
http://snapgazette.example/gisborne/issue/KLR48_19600714/t1-body-d4.html

Any design submitted should be based on the treatment of an article page such as the above.

Given the large number of pages on our site, we need a design which can be templated to work for any content in the collection, i.e. we cannot hand-craft our templates to match a given page of content, rather a template must work acceptably well for all content.

The current site, although basic in design, has the advantage that it is quite efficient in the amount of data per page request (around 100k - 200k). While not adverse to web fonts, banner imagery etc, we will carefully consider the benefit gained from any such treatment against the amount of extra data that needs to be downloaded to the client's browser.

For the right design, we are able ourselves to adapt it to a CSS layout.

An example of each core page type is as follows (though for this project we only expect a design for a single page, as itemised above):

http://snapgazette.example/gisborne/index.html
http://snapgazette.example/gisborne/about.html
http://snapgazette.example/gisborne/help.html
http://snapgazette.example/gisborne/initial/index.html
http://snapgazette.example/gisborne/search/results?type=section&text=smith&cmdSubmit=Go
http://snapgazette.example/gisborne/advanced-search/index.html
http://snapgazette.example/gisborne/issue/KLR48_19600714/t1-front-d1.html
http://snapgazette.example/gisborne/issue/KLR48_19600714/index.html
http://snapgazette.example/gisborne/issue/KLR48_19600714/fig-KLR48_19600714_005a.html
http://snapgazette.example/gisborne/issue/KLR48_19600714/KLR48_19600714_012.html
http://snapgazette.example/gisborne/issue/KLR48_19600714/thumbnails.html

Target Market(s)

A general browsing audience of all ages, but skewed towards the older generations, and those interested in family / regional history.

The average user will not be particularly web-savy, and the treatment of the content should not detract / distract from the actual content itself.

Industry/Entity Type

Events

Requirements
Must have
• * it is visually appealing
The content should be visually appealing to the audience, which can be defined as a general browsing audience of all ages, but skewed towards the middle and older generations.

* it is responsive (the design can be adapted - by us - to work in browsers across all manner of devices)

The magazine covers (http://snapgazette.example/gisborne/issues/index.html) offer some possible inspiration for treatment of the material.

```html
<!DOCTYPE html>
<html lang="en">
<head>
<meta charset="utf-8">
<title>Flying Sisters from Gisborne – Snap Gazette</title>
<link rel="stylesheet" href="https://fonts.googleapis.com/css2?family=Open+Sans:ital,wght@0,400;0,600;0,700;1,400&display=swap">
<style>
:root{
  --brand:#c93b51;
  --brand-dark:#b9334a;
  --ink:#222;
  --text:#666;
  --muted:#888;
  --panel:#e8e7e6;
  --bar:#1d1d1d;
  --footer:#4a4a4a;
  --footer-bottom:#2e2e2e;
  --rule:#c9c9c9;
}
*{box-sizing:border-box;margin:0;padding:0}
html,body{width:1056px;height:1200px;overflow:hidden}
body{font-family:"Open Sans",sans-serif;background:#fff;color:var(--ink);position:relative}
a{color:inherit;text-decoration:none}

.masthead{height:103px;background:var(--brand);position:relative}
.brand{position:absolute;left:115px;top:34px;color:#fff;font-size:26px;font-weight:700;letter-spacing:.5px}
.utility{position:absolute;left:484px;top:25px;color:#fff;font-size:10px;letter-spacing:.2px}
.utility span{margin:0 4px}
.search{position:absolute;left:726px;top:17px;width:216px;height:29px;border:1px solid rgba(255,255,255,.35);border-radius:3px;display:flex}
.search-btn{width:29px;background:var(--brand-dark);display:flex;align-items:center;justify-content:center;border-radius:3px 0 0 3px}
.search-field{flex:1;font-size:11px;font-style:italic;color:rgba(255,255,255,.85);padding:7px 0 0 17px}

.mainnav{height:35px;background:var(--bar);display:flex;justify-content:flex-end;padding-right:114px;gap:34px;align-items:center}
.mainnav a{color:#fff;font-size:12px}

.feature{position:absolute;top:173px;left:115px;width:827px;height:372px}
.spread{position:absolute;left:0;top:0;width:577px;height:372px;background:#8a8a8a;padding:6px}
.spread-img{width:100%;height:100%;background:linear-gradient(90deg,#cfcfcc 0%,#9b9b98 40%,#d8d8d5 50%,#a3a39f 70%,#c9c9c6 100%)}
.arrow{position:absolute;top:176px;width:28px;height:28px;border-radius:50%;background:rgba(30,30,30,.65);border:1px solid #ddd;display:flex;align-items:center;justify-content:center}
.arrow.prev{left:31px}.arrow.next{left:523px}
.story-panel{position:absolute;left:590px;top:0;width:237px;height:372px;background:var(--panel);padding:34px 28px 0}
.story-title{color:var(--brand);font-size:21px;font-weight:400;line-height:25px;padding-bottom:10px;border-bottom:1px solid #b8b8b8}
.story-issue{font-size:15px;padding:10px 0 11px;border-bottom:1px solid #b8b8b8}
.story-action{display:flex;align-items:center;gap:8px;font-size:12px;margin-top:13px}
.story-action.votes{color:var(--brand);margin-top:20px}
.next-link{position:absolute;left:28px;top:238px;width:186px;border-top:1px solid #b8b8b8;padding-top:20px;color:var(--brand);font-size:15px;display:flex;gap:10px;align-items:center}
.fold{position:absolute;right:0;bottom:0}

.cards{position:absolute;top:582px;left:113px;width:830px}
.card{position:absolute;top:0;width:254px}
.card-img{height:153px;border:1px solid #999}
.card-date{margin-top:23px;font-size:10px;color:var(--muted)}
.card-text{margin-top:9px;font-size:11.6px;line-height:14px;color:var(--text);text-align:justify}
.card-head{color:var(--text);font-weight:600;text-transform:uppercase}
.read-more{position:absolute;top:273px;right:0;color:var(--brand);font-size:12px}

.divider{position:absolute;top:925px;left:116px;width:824px;border-top:1px solid var(--rule)}
.partners{position:absolute;top:952px;left:113px;width:830px;height:64px;display:flex;justify-content:space-between;align-items:center}
.partner{font-size:13px;font-weight:700;color:#444;display:flex;align-items:center;gap:6px;width:120px;justify-content:center;text-align:center;line-height:15px}
.partner .dot{width:14px;height:14px;border-radius:50%;background:#e38a2b;flex:none}
.partner.red{color:var(--brand)}

.site-footer{position:absolute;top:1045px;left:0;width:1056px;height:108px;background:var(--footer)}
.footer-col{position:absolute;top:11px}
.footer-col h3{color:var(--brand);font-size:13px;font-weight:600;margin-bottom:8px}
.footer-col li{list-style:none;color:#fff;font-size:10px;line-height:11.6px;padding-left:2px}
.newsletter{position:absolute;left:598px;top:30px;width:344px}
.newsletter p{color:#fff;font-size:12px;margin-bottom:10px}
.newsletter-form{display:flex;height:33px}
.newsletter-input{flex:1;background:#e4e4e4;color:#888;font-style:italic;font-size:11px;padding:8px 12px;margin-left:2px}
.newsletter-btn{width:84px;background:var(--brand);color:#fff;font-size:15px;display:flex;align-items:center;justify-content:center}

.legal{position:absolute;top:1153px;left:0;width:1056px;height:47px;background:var(--footer-bottom)}
.license{position:absolute;left:113px;top:10px;width:73px;height:25px;background:#ddd;border:2px solid #111}
.copyright{position:absolute;left:203px;top:16px;color:#aaa;font-size:12px}
.social{position:absolute;right:114px;top:11px;display:flex;gap:3px}
.social span{width:22px;height:22px;border-radius:50%;background:#888}
</style>
</head>
<body>

<header class="masthead">
  <a class="brand" href="#">Snap Gazette</a>
  <nav class="utility">ADVANCED SEARCH<span>|</span>HELP<span>|</span>REPORT AN ERROR</nav>
  <div class="search">
    <div class="search-btn"><svg width="15" height="15" viewBox="0 0 16 16"><circle cx="6.5" cy="6.5" r="4.8" fill="none" stroke="#fff" stroke-width="2.2"/><line x1="10" y1="10" x2="14.5" y2="14.5" stroke="#fff" stroke-width="2.6" stroke-linecap="round"/></svg></div>
    <div class="search-field">Search Snap Gazette</div>
  </div>
</header>

<nav class="mainnav">
  <a href="#">HOME</a><a href="#">ABOUT</a><a href="#">BROWSE</a><a href="#">SNAP GAZETTE</a><a href="#">A-Z PEOPLE</a>
</nav>

<section class="feature">
  <div class="spread">
    <div class="spread-img" role="img" aria-label="Scanned magazine spread: engagement portraits, three air hostess sisters, a hostess in an aircraft doorway and the old highway bridge"></div>
  </div>
  <a class="arrow prev" href="#"><svg width="10" height="14" viewBox="0 0 10 14"><path d="M7 1 L2 7 L7 13" fill="none" stroke="#fff" stroke-width="1.3"/></svg></a>
  <a class="arrow next" href="#"><svg width="10" height="14" viewBox="0 0 10 14"><path d="M3 1 L8 7 L3 13" fill="none" stroke="#fff" stroke-width="1.3"/></svg></a>

  <aside class="story-panel">
    <h1 class="story-title">FLYING SISTERS FROM GISBORNE</h1>
    <p class="story-issue">NO 73 JULY 14, 1960</p>
    <p class="story-action"><svg width="18" height="18" viewBox="0 0 18 18"><circle cx="13" cy="4" r="3" fill="#555"/><circle cx="4" cy="9" r="3" fill="#555"/><circle cx="13" cy="14" r="3" fill="#555"/><path d="M13 4 L4 9 L13 14" stroke="#555" stroke-width="1.8" fill="none"/></svg>SHARE STORY</p>
    <p class="story-action votes"><svg width="18" height="18" viewBox="0 0 18 18"><rect x="1" y="8" width="4" height="9" fill="#555"/><path d="M6 8 L9 2 Q11 1 11 4 L10 7 L16 7 Q17.5 8 16.5 10 L15 16 Q14.5 17 13 17 L6 17 Z" fill="#555"/></svg>212 VOTES</p>
    <a class="next-link" href="#">NEXT ARTICLE <svg width="9" height="16" viewBox="0 0 9 16"><path d="M1 1 L8 8 L1 15" fill="none" stroke="#333" stroke-width="1.4"/></svg></a>
    <svg class="fold" width="144" height="70" viewBox="0 0 144 70"><polygon points="72,0 72,70 0,70" fill="#c9c9c7"/><polygon points="72,0 144,0 72,70" fill="var(--brand)"/></svg>
  </aside>
</section>

<section class="cards">
  <article class="card" style="left:0">
    <div class="card-img" role="img" aria-label="Photo of three smiling sisters in air hostess uniforms" style="background:linear-gradient(135deg,#bdbdbb,#3c3c3c)"></div>
    <p class="card-date">No 73 July 14, 1960</p>
    <p class="card-text">This is probably something of a record--three sisters who are all air hostesses. They are the Hallam sisters.....Marette, Ilsa, and Lorraine, daughters of Mr and Mrs R. T. Hallam, Bush-mere Road, Gisborne.</p>
    <a class="read-more" href="#">Read more</a>
  </article>
  <article class="card" style="left:288px">
    <div class="card-img" role="img" aria-label="Photo of an air hostess smiling from an aircraft doorway" style="background:linear-gradient(135deg,#d0d0ce,#555)"></div>
    <p class="card-date">No 73 July 14, 1960</p>
    <p class="card-text">And this young lady, Edith Calloway, of Auckland, has made history in another way. She was the first air hostess to make a scheduled flight to Gisborne, on Sunday of last week. Hostess ser-vice has been extended by T.A.S....</p>
    <a class="read-more" href="#" style="right:4px">Read more</a>
  </article>
  <article class="card" style="left:575px">
    <div class="card-img" role="img" aria-label="Photo of the old timber highway bridge across a river" style="background:linear-gradient(180deg,#cfcfcd,#7d7d7b 60%,#b5b5b3)"></div>
    <p class="card-date">No 73 July 14, 1960</p>
    <p class="card-text"><span class="card-head">Bridge in splints</span><br>The old highway bridge across the Waiapu River near Ruatoria probably has more Bailey "splints" than any other bridge in the country. It is to be replaced soon by ...</p>
    <a class="read-more" href="#" style="right:6px">Read more</a>
  </article>
</section>

<div class="divider"></div>
<section class="partners">
  <span class="partner"><span class="dot"></span>PageVault</span>
  <span class="partner">Harbourside Book Fund</span>
  <span class="partner">Keystone Trust</span>
  <span class="partner">Eastbay District</span>
  <span class="partner">Tidewater Library</span>
  <span class="partner red">Halloway Heritage Fund</span>
</section>

<footer class="site-footer">
  <div class="footer-col" style="left:115px">
    <h3>MENU LINKS</h3>
    <ul><li>BLOG</li><li>ABOUT US</li><li>A-Z PEOPLE</li><li>HELP</li></ul>
  </div>
  <div class="footer-col" style="left:251px">
    <h3>QUICK LINKS</h3>
    <ul><li>HOME</li><li>FOR SALE</li><li>NEWS &amp; EVENTS</li><li>CONTACT US</li></ul>
  </div>
  <div class="newsletter">
    <p>Sign in to Subscribe newsletter</p>
    <div class="newsletter-form"><div class="newsletter-input">enter your mail address</div><div class="newsletter-btn">submit</div></div>
  </div>
</footer>

<div class="legal">
  <div class="license"></div>
  <p class="copyright">2014 © Copyright snapgazette .&nbsp; All Rights Reserved</p>
  <div class="social"><span></span><span></span><span></span><span></span></div>
</div>

</body>
</html>
```